Business Card Design

We need a design for business cards for our company. We have a logo. We teach EMT's and we are based out of Virginia. The information that will need to add would be, name, title, phone number, email, address. On the back of the business card would be "We help you, help others"

Target Market(s)

People that want to become EMT's

Colors

Designer to choose colors to be used in the design.

Requirements
Must have
• company logo

```html
<!DOCTYPE html>
<html lang="en">
<head>
<meta charset="utf-8">
<title>Rescue Ready Academy – Business Card</title>
<link href="https://fonts.googleapis.com/css2?family=Montserrat:wght@600&family=Roboto:wght@300;400&display=swap" rel="stylesheet">
<style>
  :root {
    --backdrop: #d8cfc5;
    --card-light: #eeebe8;
    --card-mid: #dcd8d4;
    --brand-red: #9e1b22;
    --band-red: #a3242b;
    --band-rose: #b98a86;
    --ink-dark: #2a2a2c;
    --ink-grey: #3b3b3d;
    --band-black: #1c1d20;
    --contact-tan: #d6c1a2;
    --icon-ring: #cdb896;
  }
  * { margin: 0; padding: 0; box-sizing: border-box; }
  html, body { width: 1200px; height: 970px; overflow: hidden; }
  body { background: var(--backdrop); position: relative; }

  .business-card {
    position: absolute;
    left: 100px; top: 200px;
    width: 1000px; height: 570px;
    border-radius: 28px;
    overflow: hidden;
    background: linear-gradient(160deg, var(--card-light) 0%, var(--card-mid) 100%);
    box-shadow: 0 18px 40px rgba(0,0,0,0.18);
  }
  .card-band { position: absolute; inset: 0; }

  .brand {
    position: absolute; left: 62px; top: 92px;
    display: flex; align-items: center; gap: 22px;
    font-family: "Montserrat", sans-serif; font-weight: 600;
    color: var(--brand-red);
  }
  .brand-dot {
    width: 64px; height: 64px; border-radius: 50%;
    background: var(--brand-red);
  }
  .brand-name { line-height: 1; }
  .brand-name .line-1 { display: block; font-size: 50px; letter-spacing: -0.5px; }
  .brand-name .line-2 { display: block; font-size: 28px; letter-spacing: 13px; margin-top: 8px; }

  .person { position: absolute; left: 62px; top: 280px; }
  .person-name {
    font-family: "Montserrat", sans-serif; font-weight: 600;
    font-size: 31px; color: var(--ink-dark); letter-spacing: -0.3px;
  }
  .person-name .first { color: var(--brand-red); margin-right: 8px; }
  .person-title {
    font-family: "Roboto", sans-serif; font-weight: 400;
    font-size: 24px; color: var(--ink-grey); margin-top: 2px;
  }

  .contact {
    position: absolute; right: 46px; top: 330px;
    font-family: "Roboto", sans-serif; font-weight: 300;
    font-size: 24px; color: var(--contact-tan);
    text-align: right; letter-spacing: 0.3px;
  }
  .address p { line-height: 37px; }
  .address { margin-bottom: 10px; }
  .contact-line {
    display: flex; justify-content: flex-end; align-items: center;
    gap: 12px; height: 39px;
  }
  .contact-line svg { width: 32px; height: 32px; flex: none; }
</style>
</head>
<body>
  <div class="business-card">
    <svg class="card-band" viewBox="0 0 1000 570" preserveAspectRatio="none" role="img" aria-label="Decorative lower band in red, rose and black tones">
      <defs>
        <linearGradient id="bandFill" x1="0" y1="0" x2="1" y2="0">
          <stop offset="0" stop-color="var(--band-red)"/>
          <stop offset="0.3" stop-color="var(--band-rose)"/>
          <stop offset="0.55" stop-color="var(--band-black)"/>
          <stop offset="1" stop-color="var(--band-black)"/>
        </linearGradient>
      </defs>
      <path d="M0,400 C250,470 450,380 620,300 C760,240 880,250 1000,240 L1000,570 L0,570 Z" fill="url(#bandFill)"/>
    </svg>

    <div class="brand">
      <span class="brand-dot"></span>
      <div class="brand-name">
        <span class="line-1">RESCUE READY</span>
        <span class="line-2">ACADEMY</span>
      </div>
    </div>

    <div class="person">
      <div class="person-name"><span class="first">JORDAN</span>T. ELLIS</div>
      <div class="person-title">Managing Director</div>
    </div>

    <div class="contact">
      <div class="address">
        <p>PO Box 418, Linden Avenue</p>
        <p>Harbor Street, Richmond</p>
      </div>
      <div class="contact-line">
        <span>+1 804 555 0192</span>
        <svg viewBox="0 0 32 32" aria-hidden="true">
          <circle cx="16" cy="16" r="14.5" fill="none" stroke="var(--icon-ring)" stroke-width="2"/>
          <path d="M11.5,8.5 l3,3 -1.8,2 c1,2.2 2.6,3.8 4.8,4.8 l2-1.8 3,3 -2,2.2 c-5.6-0.6-10.4-5.4-11-11 Z" fill="var(--icon-ring)"/>
        </svg>
      </div>
      <div class="contact-line">
        <span>info@rescueready.com</span>
        <svg viewBox="0 0 32 32" aria-hidden="true">
          <circle cx="16" cy="16" r="14.5" fill="none" stroke="var(--icon-ring)" stroke-width="2"/>
          <rect x="9" y="11" width="14" height="10" rx="1" fill="var(--icon-ring)"/>
          <path d="M9.5,11.5 L16,17 L22.5,11.5" fill="none" stroke="var(--band-black)" stroke-width="1.4"/>
        </svg>
      </div>
      <div class="contact-line">
        <span>www.rescueready.com</span>
        <svg viewBox="0 0 32 32" aria-hidden="true">
          <circle cx="16" cy="16" r="14.5" fill="none" stroke="var(--icon-ring)" stroke-width="2"/>
          <g fill="none" stroke="var(--icon-ring)" stroke-width="1.4">
            <circle cx="16" cy="16" r="8"/>
            <ellipse cx="16" cy="16" rx="3.5" ry="8"/>
            <line x1="8" y1="16" x2="24" y2="16"/>
          </g>
        </svg>
      </div>
    </div>
  </div>
</body>
</html>
```